Ward Compass Business Card Design*

We need a business card design for our company Ward Compass. Our company is specialized in providing online consulting services regarding medical institutions, hospitals and doctors. We work with patients worldwide looking to choose between healthcare providers. We have a website you may use as a reference, where we list doctors and clinics worldwide. So we target Medical providers as well as patients worldwide.
Target Market(s)
Medical Providers and patients around the world
Industry/Entity Type
Medical
Contact Information for Business Card
Salwa Kettani
CEO
+90 612 348 2175
info@wardcompass.example
www.wardcompass.example
14 Annakhil 7 H.R.B. Rabat, Morocco
Requirements
Must have
- Company logo/name on one full side, personal info and smaller logo and company name on the other side.
Nice to have
- Smart and elegant design

```html
<!DOCTYPE html>
<html lang="en">
<head>
<meta charset="utf-8">
<title>Ward Compass — Business Card</title>
<link rel="stylesheet" href="https://fonts.googleapis.com/css2?family=Montserrat:wght@400;500;700&display=swap">
<style>
  :root {
    --navy: #143a67;
    --grey: #8a8a8a;
    --text-grey: #6f6f6f;
    --white: #ffffff;
    --backdrop: #d4d4d2;
  }
  * { margin: 0; padding: 0; box-sizing: border-box; }
  html, body { width: 1200px; height: 801px; overflow: hidden; }
  body {
    background: var(--backdrop);
    font-family: "Montserrat", sans-serif;
    position: relative;
  }
  .card {
    position: absolute;
    top: 252px;
    width: 520px;
    height: 297px;
    overflow: hidden;
    box-shadow: 0 6px 18px rgba(0,0,0,0.18);
  }
  .card--front { left: 60px; background: var(--white); }
  .card--back { left: 620px; background: var(--navy); }

  .front-band {
    position: absolute; left: 0; top: 0; bottom: 0;
    width: 66px; background: var(--navy);
  }
  .front-stripe {
    position: absolute; left: 66px; top: 0; bottom: 0;
    width: 8px; background: var(--grey);
  }
  .brand-dot {
    position: absolute; left: 40px; top: 28px;
    width: 64px; height: 64px; border-radius: 50%;
    background: var(--navy); border: 5px solid var(--white);
  }
  .brand-name {
    position: absolute; left: 118px; top: 44px;
    font-weight: 700; font-size: 25px; letter-spacing: 0.5px;
    color: var(--navy); text-transform: uppercase;
  }
  .person { position: absolute; left: 118px; top: 124px; }
  .person-name {
    font-weight: 700; font-size: 17px; color: var(--navy);
    text-transform: uppercase; letter-spacing: 0.3px;
  }
  .person-role {
    font-weight: 500; font-size: 14px; color: var(--text-grey);
    margin-top: 3px;
  }
  .contacts {
    position: absolute; left: 118px; top: 196px;
    list-style: none; font-size: 12px; color: var(--text-grey);
  }
  .contacts li { display: flex; align-items: center; gap: 9px; height: 22px; }
  .contacts svg { width: 12px; height: 12px; fill: var(--navy); flex: none; }
  .contacts .web-domain { color: var(--navy); }
  .address {
    position: absolute; left: 378px; top: 84px;
    padding-left: 12px; border-left: 3px solid var(--navy);
    font-size: 11.5px; line-height: 1.5; color: var(--text-grey);
  }

  .back-field { position: absolute; inset: 0; background: var(--navy); }
  .back-brand {
    position: absolute; left: 300px; top: 120px; width: 200px;
    display: flex; flex-direction: column; align-items: center; gap: 14px;
  }
  .back-brand .mark {
    width: 58px; height: 58px; border-radius: 50%; background: var(--white);
  }
  .back-brand .name {
    font-weight: 700; font-size: 17px; color: var(--white);
    text-transform: uppercase; letter-spacing: 0.5px; white-space: nowrap;
  }
</style>
</head>
<body>
  <section class="card card--front" aria-label="Card front">
    <div class="front-band"></div>
    <div class="front-stripe"></div>
    <div class="brand-dot"></div>
    <div class="brand-name">Ward Compass</div>
    <div class="person">
      <div class="person-name">Salwa Kettani</div>
      <div class="person-role">CEO</div>
    </div>
    <ul class="contacts">
      <li>
        <svg viewBox="0 0 24 24" aria-hidden="true"><path d="M6.6 10.8a15.2 15.2 0 0 0 6.6 6.6l2.2-2.2a1 1 0 0 1 1-.25 11.4 11.4 0 0 0 3.6.57 1 1 0 0 1 1 1V20a1 1 0 0 1-1 1A17 17 0 0 1 3 4a1 1 0 0 1 1-1h3.5a1 1 0 0 1 1 1c0 1.25.2 2.45.57 3.57a1 1 0 0 1-.25 1z"/></svg>
        <span>+90 612 348 2175</span>
      </li>
      <li>
        <svg viewBox="0 0 24 24" aria-hidden="true"><path d="M2 5h20v14H2z M4 7v.5l8 5 8-5V7l-8 5z" fill-rule="evenodd"/></svg>
        <span>info@wardcompass.example</span>
      </li>
      <li>
        <svg viewBox="0 0 24 24" aria-hidden="true"><circle cx="12" cy="12" r="10"/></svg>
        <span>www.<span class="web-domain">wardcompass</span>.example</span>
      </li>
    </ul>
    <address class="address" style="font-style:normal">
      14 Annakhil 7 H.R.B.<br>Rabat, Morocco
    </address>
  </section>

  <section class="card card--back" aria-label="Card back">
    <div class="back-field" role="img" aria-label="Flat navy field where a faint repeating brand pattern sits"></div>
    <div class="back-brand">
      <div class="mark"></div>
      <div class="name">Ward Compass</div>
    </div>
  </section>
</body>
</html>
```